Ward Compass Business Card Design*

We need a business card design for our company Ward Compass. Our company is specialized in providing online consulting services regarding medical institutions, hospitals and doctors. We work with patients worldwide looking to choose between healthcare providers. We have a website you may use as a reference, where we list doctors and clinics worldwide. So we target Medical providers as well as patients worldwide.
Target Market(s)
Medical Providers and patients around the world
Industry/Entity Type
Medical
Contact Information for Business Card
Salwa Kettani
CEO
+90 612 348 2175
info@wardcompass.example
www.wardcompass.example
14 Annakhil 7 H.R.B. Rabat, Morocco
Requirements
Must have
- Company logo/name on one full side, personal info and smaller logo and company name on the other side.
Nice to have
- Smart and elegant design

```html
<!DOCTYPE html>
<html lang="en">
<head>
<meta charset="utf-8">
<title>Ward Compass – Business Card</title>
<link href="https://fonts.googleapis.com/css2?family=Montserrat:wght@300;400;600;700&display=swap" rel="stylesheet">
<style>
  :root {
    --backdrop: #1e1f21;
    --brand-blue: #2a9bd3;
    --navy: #1d3461;
    --ink: #2b2d31;
    --rule: #4a4c50;
    --paper: #f7f7f8;
    --white: #ffffff;
  }
  * { box-sizing: border-box; margin: 0; padding: 0; }
  html, body {
    width: 1200px; height: 800px; overflow: hidden;
    background: var(--backdrop);
    font-family: "Montserrat", Arial, sans-serif;
  }
  .stage {
    position: relative; width: 1200px; height: 800px;
  }
  .card {
    position: absolute; left: 320px;
    width: 560px; height: 320px;
    box-shadow: 0 14px 30px rgba(0,0,0,.45);
  }
  .card--front { top: 50px; background: var(--brand-blue); }
  .card--back  { top: 430px; background: var(--paper); }

  /* Front */
  .brand-lockup {
    position: absolute; left: 92px; top: 50%;
    transform: translateY(-50%);
    display: flex; align-items: center; gap: 18px;
  }
  .brand-dot {
    width: 56px; height: 56px; border-radius: 50%;
    background: var(--white);
  }
  .brand-name {
    color: var(--white); font-weight: 400;
    font-size: 34px; letter-spacing: 2px; text-transform: uppercase;
  }

  /* Back */
  .back-mark {
    position: absolute; right: 48px; top: 36px;
    display: flex; align-items: center; gap: 10px;
  }
  .back-mark__dot {
    width: 40px; height: 40px; border-radius: 50%; background: var(--navy);
  }
  .back-mark__name {
    color: var(--navy); font-weight: 600; font-size: 17px;
  }
  .divider {
    position: absolute; left: 40px; right: 32px; top: 196px;
    height: 1px; background: var(--rule);
  }
  .person {
    position: absolute; left: 40px; top: 148px;
  }
  .person__name { font-size: 19px; color: var(--ink); font-weight: 300; letter-spacing: .5px; }
  .person__name strong { color: var(--brand-blue); font-weight: 700; }
  .person__role { font-size: 12px; color: var(--ink); font-weight: 400; margin-top: 2px; }

  .contact-list {
    position: absolute; left: 40px; top: 212px; list-style: none;
  }
  .contact-list li {
    display: flex; align-items: center; gap: 12px;
    font-size: 12.5px; color: var(--ink); height: 26px;
  }
  .contact-list svg { width: 12px; height: 12px; fill: var(--brand-blue); flex: none; }

  .company-address {
    position: absolute; right: 36px; top: 212px; text-align: right;
    font-style: normal; font-size: 12.5px; color: var(--ink); line-height: 1.65;
  }
  .company-address__name { color: var(--navy); font-weight: 600; font-size: 13.5px; }
</style>
</head>
<body>
<main class="stage">
  <section class="card card--front" aria-label="Card front">
    <div class="brand-lockup">
      <span class="brand-dot"></span>
      <span class="brand-name">Ward Compass</span>
    </div>
  </section>

  <section class="card card--back" aria-label="Card back">
    <div class="back-mark">
      <span class="back-mark__dot"></span>
      <span class="back-mark__name">Ward Compass</span>
    </div>

    <div class="person">
      <p class="person__name"><strong>SALWA</strong> KETTANI</p>
      <p class="person__role">CEO</p>
    </div>

    <div class="divider"></div>

    <ul class="contact-list">
      <li>
        <svg viewBox="0 0 24 24" aria-hidden="true"><path d="M6.6 10.8a15.1 15.1 0 0 0 6.6 6.6l2.2-2.2a1 1 0 0 1 1-.25 11.4 11.4 0 0 0 3.6.57 1 1 0 0 1 1 1V20a1 1 0 0 1-1 1A17 17 0 0 1 3 4a1 1 0 0 1 1-1h3.5a1 1 0 0 1 1 1c0 1.25.2 2.45.57 3.57a1 1 0 0 1-.25 1z"/></svg>
        +90 612 348 2175
      </li>
      <li>
        <svg viewBox="0 0 24 24" aria-hidden="true"><path d="M2 5h20v14H2z" opacity=".0"/><path d="M2 6l10 7 10-7v12H2z"/><path d="M2 4h20v1.5l-10 7-10-7z"/></svg>
        info@wardcompass.example
      </li>
      <li>
        <svg viewBox="0 0 24 24" aria-hidden="true"><path d="M12 2a10 10 0 1 0 0 20 10 10 0 0 0 0-20zm6.9 6h-2.9a15.6 15.6 0 0 0-1.4-3.6A8 8 0 0 1 18.9 8zM12 4c.8 1.2 1.5 2.5 1.9 4h-3.8c.4-1.5 1.1-2.8 1.9-4zM4.3 14a8 8 0 0 1 0-4h3.4a16 16 0 0 0 0 4zm.8 2h2.9c.3 1.3.8 2.5 1.4 3.6A8 8 0 0 1 5.1 16zM8 8H5.1a8 8 0 0 1 4.3-3.6C8.8 5.5 8.3 6.7 8 8zm4 12c-.8-1.2-1.5-2.5-1.9-4h3.8c-.4 1.5-1.1 2.8-1.9 4zm2.3-6H9.7a14.7 14.7 0 0 1 0-4h4.6a14.7 14.7 0 0 1 0 4zm.3 5.6c.6-1.1 1.1-2.3 1.4-3.6h2.9a8 8 0 0 1-4.3 3.6zM16.3 14a16 16 0 0 0 0-4h3.4a8 8 0 0 1 0 4z"/></svg>
        www.wardcompass.example
      </li>
    </ul>

    <address class="company-address">
      <span class="company-address__name">Ward Compass</span><br>
      14 Annakhil 7 H.R.B.<br>
      Rabat, Morocco
    </address>
  </section>
</main>
</body>
</html>
```